Luxury WordPress Website for CORALBASINS

I need a professional WordPress website for Coral Basins. The site should be modern, visually appealing, and user-friendly, reflecting the brand’s luxury and premium identity. It must include a homepage, product/service pages, contact form, and be responsive on both desktop and mobile devices. The design should allow for easy updates and integration of future content, while maintaining a polished and professional look.

Target Market(s)

swimmingpool & spa

Industry/Entity Type

Swimmingpool

Coding

Coded - Design and coding required

Font styles to use
Other font styles liked:
• HaboroSoft

Requirements
Must have
• Exclusive appearance
Nice to have
• • A logo that subtly incorporates water or pool elements. • A color palette that reflects luxury, elegance, and relaxation. • Clean and modern typography that is easy to read across all media. • Iconography or design elements that convey premium quality. • A versatile design that can be adapted for social media, merchandise, and promotional materials. • Optional: A tagline that emphasizes luxury and high-end pool experiences.

```html
<!DOCTYPE html>
<html lang="en">
<head>
<meta charset="UTF-8">
<title>Coral Basins — Luxury Pools</title>
<link href="https://fonts.googleapis.com/css2?family=Montserrat:wght@500;600;700;800&family=Poppins:wght@400;500;600&display=swap" rel="stylesheet">
<style>
:root{
  --blue:#0b5fb4;
  --blue-dark:#0a3f86;
  --aqua:#2bb3ea;
  --aqua-soft:#e8f6fd;
  --ink:#1b1f27;
  --muted:#5b6470;
  --white:#ffffff;
  --black:#0c0d10;
  --star:#f5b919;
}
*{box-sizing:border-box;margin:0;padding:0}
html,body{width:1200px;height:3740px;overflow:hidden}
body{font-family:'Poppins',sans-serif;color:var(--ink);background:var(--white);position:relative}
h1,h2,h3,.nav,.btn{font-family:'Montserrat',sans-serif}
.btn{display:inline-flex;align-items:center;gap:8px;background:var(--aqua);color:var(--white);font-weight:700;font-size:14px;letter-spacing:.5px;padding:12px 26px;border-radius:30px;text-decoration:none}
.btn svg{width:12px;height:12px}

/* header */
.site-header{position:absolute;top:0;left:0;width:1200px;height:88px;background:var(--white);z-index:3}
.brand{position:absolute;left:100px;top:10px;display:flex;align-items:center;gap:12px}
.brand-dot{width:44px;height:44px;border-radius:50%;background:var(--aqua)}
.brand-name{font-family:'Montserrat',sans-serif;font-weight:800;font-size:24px;color:var(--blue)}
.brand-tag{position:absolute;left:156px;top:50px;font-size:13px;color:var(--muted)}
.nav{position:absolute;left:585px;top:30px;display:flex;gap:40px;font-size:15px;font-weight:700;color:var(--ink)}
.nav a{color:inherit;text-decoration:none;padding-bottom:8px}
.nav a.active{color:var(--blue);border-bottom:3px solid var(--blue)}
.phone-pill{position:absolute;right:0;top:18px;height:52px;width:265px;background:var(--blue);border-radius:26px 0 0 26px;display:flex;align-items:center;gap:14px;padding-left:10px;color:var(--white);font-weight:600;font-size:17px}
.phone-pill .ico{width:36px;height:36px;border-radius:50%;background:var(--white);display:flex;align-items:center;justify-content:center}

/* hero */
.hero{position:absolute;top:88px;left:0;width:1200px;height:632px;background:linear-gradient(180deg,#8fbcd9 0%,#4f7d4a 30%,#3a8d55 45%,#46c0e6 60%,#1593d0 85%,#c7cdd1 100%)}
.hero-text{position:absolute;top:178px;width:100%;text-align:center;color:var(--white)}
.hero-text h1{font-size:44px;font-weight:800;line-height:54px;letter-spacing:1px;text-shadow:0 2px 6px rgba(0,0,0,.35)}
.hero-text .btn{margin-top:30px}

/* welcome */
.welcome{position:absolute;top:720px;left:0;width:1200px;height:570px}
.welcome-copy{position:absolute;left:110px;top:60px;width:460px}
.welcome-kicker{font-family:'Montserrat',sans-serif;font-size:30px;font-weight:600;color:var(--aqua);display:flex;align-items:center;gap:14px}
.welcome-kicker::after{content:"";width:60px;height:3px;background:var(--aqua)}
.welcome-copy h2{font-size:30px;font-weight:800;color:var(--blue-dark);margin-top:6px}
.welcome-copy p{font-size:14px;line-height:24px;color:var(--muted);margin-top:20px}
.welcome-copy .btn{margin-top:26px}
.welcome-frame{position:absolute;left:650px;top:90px;width:440px;height:380px;background:var(--blue);border-radius:4px}
.welcome-photo{position:absolute;left:632px;top:72px;width:440px;height:380px;border:6px solid var(--white);background:linear-gradient(160deg,#dfe7ee 0%,#7fc7e6 45%,#1d9ad6 100%);box-shadow:0 6px 20px rgba(0,0,0,.15)}

/* services */
.services{position:absolute;top:1290px;left:0;width:1200px;height:700px;background:linear-gradient(180deg,#0d63bb,#0a55a6)}
.section-title{text-align:center;font-size:36px;font-weight:800}
.services .section-title{color:var(--white);padding-top:100px}
.service-cards{position:absolute;top:188px;left:110px;display:flex;gap:25px}
.service-card{width:310px;height:415px;background:var(--white);border-radius:4px;text-align:center;overflow:hidden}
.service-img{height:200px}
.service-card h3{font-size:17px;font-weight:800;color:var(--ink);margin:22px 20px 10px;line-height:22px;text-transform:uppercase}
.service-card p{font-size:14px;line-height:21px;color:var(--muted);padding:0 26px}
.service-card .btn{margin-top:18px;font-size:13px;padding:10px 22px}
.slide-arrow{position:absolute;top:1650px;width:34px;height:34px;border-radius:50%;background:var(--white);display:flex;align-items:center;justify-content:center;z-index:2}

/* projects */
.projects{position:absolute;top:1990px;left:0;width:1200px;height:770px}
.projects .section-title{color:var(--ink);padding-top:90px}
.project-grid{position:absolute;top:170px;left:110px;display:grid;grid-template-columns:repeat(4,236px);grid-auto-rows:222px;gap:12px}
.project-grid .tile{border-radius:2px}
.projects .btn{position:absolute;left:528px;top:656px}

/* testimonials */
.testimonials{position:absolute;top:2760px;left:0;width:1200px;height:570px;background:var(--aqua-soft)}
.testimonials .section-title{color:var(--ink);padding-top:100px}
.t-cards{position:absolute;top:230px;left:110px;display:flex;gap:35px}
.t-card{position:relative;width:310px;height:240px;background:var(--white);border-radius:10px;border-top:4px solid var(--aqua);box-shadow:0 6px 18px rgba(11,95,180,.12);text-align:center;padding:80px 28px 0}
.t-avatar{position:absolute;left:115px;top:-48px;width:80px;height:80px;border-radius:50%;background:linear-gradient(160deg,#e9d4c4,#9aa7b4);border:4px solid var(--white)}
.t-card p{font-size:12px;line-height:19px;color:var(--muted)}
.t-meta{display:flex;justify-content:center;gap:16px;margin-top:18px;font-size:12px;font-style:italic;color:var(--ink)}
.stars{color:var(--star);letter-spacing:2px;font-style:normal}
.t-arrow{position:absolute;top:2975px;width:30px;height:30px;border-radius:50%;border:1px solid #9fb3c6;display:flex;align-items:center;justify-content:center}

/* footer */
.site-footer{position:absolute;top:3330px;left:0;width:1200px;height:410px;background:var(--black);color:var(--white)}
.f-brand{position:absolute;left:110px;top:60px;width:230px;text-align:center}
.f-brand .name{font-family:'Montserrat',sans-serif;font-weight:800;font-size:30px;color:var(--aqua);display:flex;align-items:center;justify-content:center;gap:10px}
.f-brand .name i{width:30px;height:30px;border-radius:50%;background:var(--aqua);display:block}
.f-brand .tag{font-size:14px;margin-top:6px}
.socials{display:flex;justify-content:center;gap:14px;margin-top:26px}
.socials span{width:30px;height:30px;border-radius:50%;background:var(--white)}
.socials span:nth-child(2){background:var(--aqua)}
.f-col{position:absolute;top:70px}
.f-col h3{font-size:15px;font-weight:800;margin-bottom:16px}
.f-col li{list-style:none;font-size:13px;line-height:26px;color:#d9dde3}
.contact-row{display:flex;gap:12px;font-size:12px;line-height:18px;color:#d9dde3;margin-bottom:14px;width:190px}
.contact-row .ico{flex:none;width:26px;height:26px;border-radius:4px;background:var(--blue);display:flex;align-items:center;justify-content:center}
.f-sub p{font-size:12px;line-height:19px;color:#d9dde3;width:250px}
.sub-form{display:flex;margin-top:18px;width:250px;height:36px}
.sub-form .field{flex:1;background:var(--white);border-radius:3px 0 0 3px;font-size:11px;color:#8a93a0;padding:10px 12px}
.sub-form .go{width:40px;background:var(--blue);border-radius:0 3px 3px 0;display:flex;align-items:center;justify-content:center}
.copyright{position:absolute;left:0;bottom:0;width:100%;height:56px;border-top:1px solid #2a2d33;text-align:center;font-size:13px;line-height:56px;color:#c9ced6}
</style>
</head>
<body>

<header class="site-header">
  <div class="brand"><span class="brand-dot"></span><span class="brand-name">CORAL BASINS</span></div>
  <div class="brand-tag">All your dreams come true</div>
  <nav class="nav"><a class="active" href="#">HOME</a><a href="#">ABOUT US</a><a href="#">SERVICES</a></nav>
  <div class="phone-pill">
    <span class="ico"><svg width="18" height="18" viewBox="0 0 24 24"><path fill="#0b5fb4" d="M6.6 10.8a15 15 0 0 0 6.6 6.6l2.2-2.2c.3-.3.7-.4 1-.2 1.1.4 2.3.6 3.6.6.6 0 1 .4 1 1V20c0 .6-.4 1-1 1A17 17 0 0 1 3 4c0-.6.4-1 1-1h3.5c.6 0 1 .4 1 1 0 1.3.2 2.5.6 3.6.1.3 0 .7-.2 1z"/></svg></span>
    +1 555 014 2290
  </div>
</header>

<section class="hero" role="img" aria-label="Backyard swimming pool with lawn and trees">
  <div class="hero-text">
    <h1>EXCEPTIONAL DESIGN.<br>EXTRAORDINARY<br>SERVICE.</h1>
    <a class="btn" href="#">GET STARTED <svg viewBox="0 0 12 12"><path d="M3 1l5 5-5 5" stroke="#fff" stroke-width="2" fill="none"/></svg></a>
  </div>
</section>

<section class="welcome">
  <div class="welcome-copy">
    <div class="welcome-kicker">WELCOME TO</div>
    <h2>CORAL BASINS COMPANY</h2>
    <p>Lorem ipsum dolor sit amet, consectetur adipiscing elit, sed do eiusmod tempor incididunt ut labore et dolore magna aliqua. Ut enim ad minim veniam, quis nostrud exercitation ullamco laboris nisi ut aliquip ex ea commodo consequat.</p>
    <p>Duis aute irure dolor in reprehenderit in voluptate velit esse cillum dolore eu fugiat nulla pariatur. Excepteur sint occaecat cupidatat non proident, sunt in culpa qui officia deserunt mollit anim id est laborum.</p>
    <a class="btn" href="#">READ MORE <svg viewBox="0 0 12 12"><path d="M3 1l5 5-5 5" stroke="#fff" stroke-width="2" fill="none"/></svg></a>
  </div>
  <div class="welcome-frame"></div>
  <div class="welcome-photo" role="img" aria-label="Pool with steel ladder and stone deck"></div>
</section>

<section class="services">
  <h2 class="section-title">OUR SERVICES</h2>
  <div class="service-cards">
    <article class="service-card">
      <div class="service-img" role="img" aria-label="Covered pool beside a large house" style="background:linear-gradient(180deg,#9cc3de,#6f8f5a 55%,#2aa3d8)"></div>
      <h3>Automatic Cover Repair<br>and Installation</h3>
      <p>Protect your pool with high-quality automatic covers installed and repaired by skilled professionals</p>
      <a class="btn" href="#">READ MORE <svg viewBox="0 0 12 12"><path d="M3 1l5 5-5 5" stroke="#fff" stroke-width="2" fill="none"/></svg></a>
    </article>
    <article class="service-card">
      <div class="service-img" role="img" aria-label="Pool being opened for the season" style="background:linear-gradient(180deg,#b7d3e6,#5f8a55 50%,#1f9bd4)"></div>
      <h3>Pool Openings and<br>Closings</h3>
      <p>Protect your pool with high-quality automatic covers installed and repaired by skilled professionals</p>
      <a class="btn" href="#">READ MORE <svg viewBox="0 0 12 12"><path d="M3 1l5 5-5 5" stroke="#fff" stroke-width="2" fill="none"/></svg></a>
    </article>
    <article class="service-card">
      <div class="service-img" role="img" aria-label="Pool equipment beside blue water" style="background:linear-gradient(180deg,#a8cde6,#3d9bd3 45%,#0f6fb9)"></div>
      <h3>Pool Equipment Repair<br>and Installation</h3>
      <p>Protect your pool with high-quality automatic covers installed and repaired by skilled professionals</p>
      <a class="btn" href="#">READ MORE <svg viewBox="0 0 12 12"><path d="M3 1l5 5-5 5" stroke="#fff" stroke-width="2" fill="none"/></svg></a>
    </article>
  </div>
</section>
<span class="slide-arrow" style="left:40px"><svg width="12" height="12" viewBox="0 0 12 12"><path d="M8 1L3 6l5 5" stroke="#0b5fb4" stroke-width="2" fill="none"/></svg></span>
<span class="slide-arrow" style="left:1126px"><svg width="12" height="12" viewBox="0 0 12 12"><path d="M4 1l5 5-5 5" stroke="#0b5fb4" stroke-width="2" fill="none"/></svg></span>

<section class="projects">
  <h2 class="section-title">OUR PROJECTS</h2>
  <div class="project-grid">
    <div class="tile" role="img" aria-label="Modern house with pool" style="background:linear-gradient(180deg,#d7dde2,#8a8f86 50%,#2fa6db)"></div>
    <div class="tile" role="img" aria-label="Resort pool with palms" style="background:linear-gradient(180deg,#6fa35c,#39b6e3 55%,#1b8bcc)"></div>
    <div class="tile" role="img" aria-label="Brick house with pool" style="background:linear-gradient(180deg,#b9d5ea,#8a5a44 45%,#2ea0d6)"></div>
    <div class="tile" role="img" aria-label="Pool with wooden deck" style="background:linear-gradient(180deg,#5e8a4b,#2a9fd7 55%,#a5693f)"></div>
    <div class="tile" role="img" aria-label="Pool by hedges" style="background:linear-gradient(180deg,#4e7d3f,#3cb1e0 60%,#cfd3d6)"></div>
    <div class="tile" role="img" aria-label="Covered terrace pool" style="background:linear-gradient(180deg,#7a5a40,#d9cdb8 40%,#35a9de)"></div>
    <div class="tile" role="img" aria-label="Pool at dusk" style="background:linear-gradient(180deg,#6d7c8d,#2b8ccb 55%,#0f5e9d)"></div>
    <div class="tile" role="img" aria-label="Garden pool with house" style="background:linear-gradient(180deg,#c8d8e4,#6b8f56 45%,#2aa5dc)"></div>
  </div>
  <a class="btn" href="#">VIEW ALL <svg viewBox="0 0 12 12"><path d="M3 1l5 5-5 5" stroke="#fff" stroke-width="2" fill="none"/></svg></a>
</section>

<section class="testimonials">
  <h2 class="section-title">CLIENT TESTIMONIALS</h2>
  <div class="t-cards">
    <article class="t-card">
      <div class="t-avatar" role="img" aria-label="Client portrait"></div>
      <p>Sed ut perspiciatis unde omnis iste natus error sit voluptatem accusantium doloremque laudantium, totam rem aperiam, eaque ipsa.</p>
      <div class="t-meta"><span>Dana Reyes</span><span class="stars">★★★★★</span></div>
    </article>
    <article class="t-card">
      <div class="t-avatar" role="img" aria-label="Client portrait"></div>
      <p>Sed ut perspiciatis unde omnis iste natus error sit voluptatem accusantium doloremque laudantium, totam rem aperiam, eaque ipsa.</p>
      <div class="t-meta"><span>Dana Reyes</span><span class="stars">★★★★★</span></div>
    </article>
    <article class="t-card">
      <div class="t-avatar" role="img" aria-label="Client portrait"></div>
      <p>Sed ut perspiciatis unde omnis iste natus error sit voluptatem accusantium doloremque laudantium, totam rem aperiam, eaque ipsa.</p>
      <div class="t-meta"><span>Dana Reyes</span><span class="stars">★★★★★</span></div>
    </article>
  </div>
</section>
<span class="t-arrow" style="left:40px"><svg width="10" height="10" viewBox="0 0 12 12"><path d="M8 1L3 6l5 5" stroke="#7d93a8" stroke-width="2" fill="none"/></svg></span>
<span class="t-arrow" style="left:1130px"><svg width="10" height="10" viewBox="0 0 12 12"><path d="M4 1l5 5-5 5" stroke="#7d93a8" stroke-width="2" fill="none"/></svg></span>

<footer class="site-footer">
  <div class="f-brand">
    <div class="name"><i></i>CORAL BASINS</div>
    <div class="tag">All your dreams come true</div>
    <div class="socials"><span></span><span></span><span></span></div>
  </div>
  <div class="f-col" style="left:440px">
    <h3>QUICK LINKS</h3>
    <ul><li>Home</li><li>Services</li><li>About Us</li><li>Gallery</li><li>Testimonials</li><li>About Us</li></ul>
  </div>
  <div class="f-col" style="left:615px">
    <h3>CONTACT US</h3>
    <div class="contact-row"><span class="ico"><svg width="13" height="13" viewBox="0 0 24 24"><path fill="#fff" d="M6.6 10.8a15 15 0 0 0 6.6 6.6l2.2-2.2c.3-.3.7-.4 1-.2 1.1.4 2.3.6 3.6.6.6 0 1 .4 1 1V20c0 .6-.4 1-1 1A17 17 0 0 1 3 4c0-.6.4-1 1-1h3.5c.6 0 1 .4 1 1 0 1.3.2 2.5.6 3.6.1.3 0 .7-.2 1z"/></svg></span><span>555-014-7731</span></div>
    <div class="contact-row"><span class="ico"><svg width="13" height="13" viewBox="0 0 24 24"><path d="M3 6h18v12H3z M3 6l9 7 9-7" stroke="#fff" stroke-width="2" fill="none"/></svg></span><span>hello@coralbasins.com</span></div>
    <div class="contact-row"><span class="ico"><svg width="13" height="13" viewBox="0 0 24 24"><path fill="#fff" d="M12 2a7 7 0 0 0-7 7c0 5 7 13 7 13s7-8 7-13a7 7 0 0 0-7-7zm0 9.5A2.5 2.5 0 1 1 12 6.5a2.5 2.5 0 0 1 0 5z"/></svg></span><span>418 Lagoon Way,<br>Bayview, CA 90210</span></div>
  </div>
  <div class="f-col f-sub" style="left:840px">
    <h3>SUBSCRIBE TO OUR BLOG</h3>
    <p>Sign up today to get resources on how to attract and retain more customers</p>
    <div class="sub-form"><span class="field">Enter email address</span><span class="go"><svg width="14" height="14" viewBox="0 0 24 24"><path fill="#fff" d="M2 21l21-9L2 3v7l15 2-15 2z"/></svg></span></div>
  </div>
  <div class="copyright">©2025 Company Name, All Rights Reserved</div>
</footer>

</body>
</html>
```